New Webpage for High Class Expert Witness Services Company

We are looking for a minimalist design for a webpage that just has our logo and an entry form offer to connect with one of our Liaisons.
The entry form should just ask for Name, Email, Contact Info and Description of Project.

Company Name is: The Marlowe Crest Advisory Services

Number of Pages Required

1 page

```html
<!DOCTYPE html>
<html lang="en">
<head>
<meta charset="utf-8">
<title>The Marlowe Crest Advisory Services — Connect With a Liaison</title>
<link rel="stylesheet" href="https://fonts.googleapis.com/css2?family=Cinzel:wght@400&family=Playfair+Display:wght@400;700&family=Roboto:wght@400&display=swap">
<style>
  :root {
    --page-bg: #111111;
    --pattern-dark: #141414;
    --pattern-light: #2a2a2a;
    --card-bg: #121212;
    --card-border: #d9d9d9;
    --brand-panel: #161616;
    --brand-text: #cfcfcf;
    --brand-mark: #9d9d9d;
    --heading: #d8d8d8;
    --body-text: #ffffff;
    --label: #ffffff;
    --field-bg: #ffffff;
    --placeholder: #9a9a9a;
    --button-bg: #c1c2c4;
    --button-text: #1a1a1a;
    --footer-text: #d6cdb9;
  }
  * { box-sizing: border-box; margin: 0; padding: 0; }
  html, body {
    width: 1200px; height: 1008px; overflow: hidden; background: #ffffff;
  }
  .page { position: relative; width: 1200px; height: 1008px; }
  .backdrop {
    position: absolute; left: 0; top: 0; width: 1200px; height: 981px;
    background:
      radial-gradient(ellipse at 8% 30%, var(--pattern-light) 0%, transparent 45%),
      radial-gradient(ellipse at 92% 70%, var(--pattern-light) 0%, transparent 45%),
      linear-gradient(135deg, var(--pattern-dark), #1d1d1d 50%, var(--pattern-dark));
  }
  .card {
    position: absolute; left: 211px; top: 34px; width: 780px; height: 879px;
    background: var(--card-bg);
    border: 1px solid var(--card-border);
    border-radius: 19px;
  }
  .brand {
    position: absolute; left: 29px; top: 32px; width: 721px; height: 145px;
    background: var(--brand-panel);
    display: flex; align-items: center; justify-content: center; gap: 18px;
  }
  .brand-mark { width: 34px; height: 34px; background: var(--brand-mark); }
  .brand-name {
    font-family: "Cinzel", serif; font-weight: 400; font-size: 25px;
    letter-spacing: 1px; color: var(--brand-text); text-transform: uppercase;
    white-space: nowrap;
  }
  .intro-title {
    position: absolute; left: 0; top: 266px; width: 100%;
    text-align: center;
    font-family: "Cinzel", serif; font-weight: 400; font-size: 28px;
    color: var(--heading); line-height: 36px;
  }
  .intro-text {
    position: absolute; left: 29px; top: 308px; width: 721px;
    font-family: "Roboto", sans-serif; font-size: 13.6px; line-height: 20.3px;
    color: var(--body-text); text-align: justify;
  }
  .contact-form {
    position: absolute; left: 29px; top: 372px; width: 720px; height: 398px;
    border: 1px solid var(--card-border); border-radius: 19px;
    padding: 27px 29px 0;
  }
  .field-label {
    display: block; height: 16px; margin-bottom: 8px;
    font-family: "Playfair Display", serif; font-weight: 700; font-size: 13px;
    line-height: 16px; color: var(--label); text-transform: uppercase;
  }
  .field-input, .field-area {
    display: block; width: 100%; border: none; border-radius: 2px;
    background: var(--field-bg);
    font-family: "Roboto", sans-serif; font-size: 12px; color: #222;
    margin-bottom: 8px;
  }
  .field-input { height: 33px; padding: 0 14px; }
  .field-area { height: 80px; padding: 10px 12px; resize: vertical; margin-bottom: 10px; }
  .field-input::placeholder, .field-area::placeholder { color: var(--placeholder); }
  .submit-button {
    display: block; width: 100%; height: 32px; border: none; border-radius: 2px;
    background: var(--button-bg); color: var(--button-text);
    font-family: "Playfair Display", serif; font-size: 13px; text-transform: uppercase;
  }
  .site-footer {
    position: absolute; left: 0; top: 830px; width: 100%; text-align: center;
    font-family: "Playfair Display", serif; font-size: 14px;
    font-variant: small-caps; color: var(--footer-text);
  }
</style>
</head>
<body>
<div class="page">
  <div class="backdrop" role="img" aria-label="Dark faceted geometric triangle pattern background"></div>
  <main class="card">
    <header class="brand">
      <span class="brand-mark"></span>
      <span class="brand-name">The Marlowe Crest Advisory Services</span>
    </header>
    <h1 class="intro-title">CONNECT WITH ONE OF OUR LIAISONS</h1>
    <p class="intro-text">Lorem ipsum dolor sit amet, consectetur adipiscing elit, sed do eiusmod tempor incididunt ut labore et dolore magna aliqua. Vulputate dignissim suspendisse in est ante. Faucibus turpis in eu mi bibendum neque. Sodales ut etiam sit amet nisl purus. Velit laoreet id donec ultrices tincidunt.</p>
    <form class="contact-form">
      <label class="field-label" for="name">Name</label>
      <input class="field-input" id="name" type="text" placeholder="Name">
      <label class="field-label" for="email">Email</label>
      <input class="field-input" id="email" type="email" placeholder="Type your Email">
      <label class="field-label" for="contact">Contact Info</label>
      <input class="field-input" id="contact" type="text" placeholder="Type your contact information">
      <label class="field-label" for="project">Description of Project</label>
      <textarea class="field-area" id="project" placeholder="Describe about your project."></textarea>
      <button class="submit-button" type="submit">Submit</button>
    </form>
    <footer class="site-footer">Copyright © 2026 &amp; Powered by The Marlowe Crest Advisory Services</footer>
  </main>
</div>
</body>
</html>
```